Flyer Design Project

I require a double sided flyer in PSD format.
The flyer should look fresh and clean.
The flyer is for an digital marketing company that offers various services. The services are broken down into 3 main categories and the design should reflect this.
All the content is provided in the attached file
Industry/Entity Type
Digital
Requirements
Must have
- Front of the leaflet to be mainly white background with appealing text based questions in the colours in large font with relevant images.
Back if the
3 separate boxes using the colours indicated in the attachment for the services on back of the leafet.
Should not have
- Gradients
Borders on the edges of the design
Vignettes
Black elements
Any text below 10pt
Fancy fonts
Do not use old-style fonts

```html
<!DOCTYPE html>
<html lang="en">
<head>
<meta charset="utf-8">
<title>Brightlane – Digital Marketing Flyer</title>
<link href="https://fonts.googleapis.com/css2?family=Russo+One&family=Arimo:wght@400;700&family=Exo+2:wght@400;500&display=swap" rel="stylesheet">
<style>
  :root{
    --stage:#141414;
    --paper:#ffffff;
    --lime:#b8d432;
    --lime-deep:#9cc43b;
    --sky:#2cc1ef;
    --sky-deep:#1b6fc0;
    --sun:#fcc34a;
    --orange:#f39634;
    --orange-deep:#e8741f;
    --coupon-green:#1f9a3e;
    --navy:#1b3a78;
    --grey:#9d9d9f;
    --grey-text:#6e6e70;
    --label:#9a9a9a;
    --art:#dff2fb;
    --head:"Russo One", sans-serif;
    --body:"Arimo", sans-serif;
    --soft:"Exo 2", sans-serif;
  }
  *{box-sizing:border-box;margin:0;padding:0}
  html,body{width:1200px;height:736px;overflow:hidden;background:var(--stage)}
  .stage{position:relative;width:1200px;height:736px}
  .side-label{position:absolute;font-family:var(--body);font-weight:700;font-size:14px;color:var(--label)}

  /* FRONT */
  .front{position:absolute;left:88px;top:84px;width:400px;height:580px;background:var(--paper);overflow:hidden}
  .hero-art{position:absolute;left:56px;top:12px;width:290px;height:206px;background:var(--art)}
  .band{position:absolute;transform:skewY(-2.5deg);font-family:var(--head);color:#fff;text-transform:uppercase;line-height:1;white-space:nowrap}
  .band small{display:block;font-size:8px;letter-spacing:.5px}
  .band-lime{left:0;top:232px;width:400px;height:62px;background:var(--lime);padding:6px 10px 0 78px}
  .band-lime .big{font-size:22px}
  .band-lime .mid{font-size:14px;padding-left:44px}
  .band-lime small.indent{padding-left:86px}
  .band-sky{left:0;top:316px;width:372px;height:38px;background:var(--sky);padding:6px 0 0 42px}
  .band-sky .mid{font-size:16px}
  .band-sun{left:18px;top:366px;width:382px;height:50px;background:var(--sun);padding:4px 8px 0 168px}
  .band-sun .big{font-size:18px;letter-spacing:-.3px}
  .band-sun small.indent{padding-left:60px;font-size:10px}
  .tagline{position:absolute;left:40px;top:458px;font-family:var(--soft);font-size:17px;color:var(--grey-text);text-align:right;line-height:1.15;width:240px}
  .brand-mark{position:absolute;left:292px;top:420px;width:98px;height:98px;border-radius:50%;background:var(--grey);
    display:flex;align-items:center;justify-content:center;font-family:var(--body);font-weight:700;font-size:15px;color:#fff}
  .front-call{position:absolute;left:28px;top:546px;width:372px;height:22px;background:var(--grey);
    font-family:var(--body);font-weight:700;font-size:14px;color:#fff;padding:2px 0 0 30px;white-space:nowrap}

  /* BACK */
  .back{position:absolute;left:548px;top:168px;width:608px;height:436px;background:var(--paper);overflow:hidden}
  .service{position:absolute;top:32px;width:176px;height:300px;padding:12px 10px 0 14px;color:#fff}
  .service-consult{left:28px;background:var(--lime-deep)}
  .service-design{left:216px;background:var(--sky)}
  .service-sem{left:404px;background:var(--orange)}
  .service h2{font-family:var(--head);font-weight:400;text-align:center;font-size:21px;line-height:1.05;margin-bottom:12px;text-transform:uppercase}
  .service h2 span{display:block;font-size:16px}
  .service ul{list-style:none;font-family:var(--body);font-weight:700;font-size:11px}
  .service li{position:relative;padding-left:16px;margin-bottom:11px;line-height:1.2}
  .service-sem li{margin-bottom:3px}
  .service li::before{content:"";position:absolute;left:0;top:1px;width:9px;height:9px;border:1px solid #fff}
  .service li::after{content:"";position:absolute;left:3px;top:2px;width:3px;height:6px;border:solid #fff;border-width:0 2px 2px 0;transform:rotate(45deg)}
  .coupon{position:absolute;left:16px;right:16px;bottom:14px;height:84px;border:2px dashed var(--navy);
    text-align:center;color:#fff;font-family:var(--body);font-weight:700;padding-top:6px}
  .coupon strong{display:block;font-size:40px;line-height:1}
  .coupon span{font-size:16px}
  .coupon-green{background:var(--coupon-green)}
  .coupon-blue{background:var(--sky-deep)}
  .coupon-orange{background:var(--orange-deep)}
  .coupon-orange strong{font-size:30px}
  .coupon-orange span{font-size:13px}
  .back-mark{position:absolute;left:74px;top:356px;width:62px;height:62px;border-radius:50%;background:var(--grey);
    display:flex;align-items:center;justify-content:center;font-family:var(--body);font-weight:700;font-size:10px;color:#fff}
  .divider{position:absolute;left:162px;top:354px;width:1px;height:60px;background:var(--sky-deep)}
  .address{position:absolute;left:190px;top:344px;font-family:var(--body);font-size:12px;color:var(--sky-deep);line-height:1.3}
  .address strong{font-size:14px}
  .back-call{position:absolute;left:300px;top:310px;width:280px;height:54px;background:var(--grey);color:#fff;
    font-family:var(--body);font-weight:700;text-align:center;padding-top:6px;line-height:1.1}
  .back-call strong{display:block;font-size:20px}
  .back-call span{font-size:13px}
  .back-call{top:310px}
</style>
</head>
<body>
<main class="stage">
  <p class="side-label" style="left:266px;top:56px">Front</p>
  <p class="side-label" style="left:814px;top:146px">Back</p>

  <section class="front">
    <div class="hero-art" role="img" aria-label="Illustration of a globe connected to people and laptops"></div>
    <div class="band band-lime">
      <small>Did you know</small>
      <div class="big">85% of consumers</div>
      <small class="indent">Use the internet</small>
      <div class="mid">to find businesses like yours?</div>
    </div>
    <div class="band band-sky">
      <small>Are your</small>
      <div class="mid">customers finding you online?</div>
    </div>
    <div class="band band-sun">
      <small>Do you need</small>
      <div class="big">more customers</div>
      <small class="indent">for your business?</small>
    </div>
    <p class="tagline">Let us help you<br>grow your business online</p>
    <div class="brand-mark">Brightlane</div>
    <p class="front-call">Call 0100 555 0142 for a FREE consultation</p>
  </section>

  <section class="back">
    <article class="service service-consult">
      <h2>Consulting<span>Services</span></h2>
      <ul>
        <li>Marketing Strategy And Planning</li>
        <li>Business Branding</li>
        <li>Competition Analysis</li>
      </ul>
      <div class="coupon coupon-green"><strong>FREE</strong><span>Consultation</span></div>
    </article>
    <article class="service service-design">
      <h2>Design<span>Services</span></h2>
      <ul>
        <li>Web Design</li>
        <li>Website Maintenance</li>
        <li>Logo Design</li>
        <li>Flyer Design</li>
      </ul>
      <div class="coupon coupon-blue"><strong>FREE</strong><span>Website</span></div>
    </article>
    <article class="service service-sem">
      <h2>SEM<span>Services</span></h2>
      <ul>
        <li>Local Business Marketing</li>
        <li>Ppc</li>
        <li>Email Marketing</li>
        <li>Seo</li>
        <li>Social Media</li>
        <li>Content Development</li>
        <li>Website Audit</li>
        <li>Lead Generation</li>
      </ul>
      <div class="coupon coupon-orange"><strong>25% OFF</strong><span>any SEM Package</span></div>
    </article>
    <div class="back-mark">Brightlane</div>
    <div class="divider"></div>
    <p class="address"><strong>Brightlane</strong><br>12 Harbour Row<br>Millford<br>MF1 4QT</p>
    <p class="back-call" style="top:352px"><strong>Call 0100 555 0199</strong><span>for a FREE consultation</span></p>
  </section>
</main>
</body>
</html>
```